iPhone iOS 7 App For Managing Tasks/Photos for Internal Company Use

We need an app design that displays company objectives and task, and provides the interface for employees to complete a task by uploading a photo and adding comments.

Please see attached mock up sketches as a rough guideline

Final delivery of files must contain PSD, and all layers/objects sliced both is PSD and PNG files

Target Market(s)

This is a tool for internal employee use

Industry/Entity Type

It Company

Requirements
Must have
• Must include logo, and match the colour scheme
Use iPhone iOS 7 Style

```html
<!DOCTYPE html>
<html lang="en">
<head>
<meta charset="utf-8">
<title>Home – Objectives</title>
<link rel="stylesheet" href="https://fonts.googleapis.com/css2?family=Roboto:wght@300;400;500&display=swap">
<style>
  :root {
    --screen-bg: #f5f5f5;
    --bar-bg: #ffffff;
    --divider: #e3e3e3;
    --ink: #111111;
    --ring-track: #a8bfcb;
    --core: #466769;
    --core-text: #ffffff;
    --tab-bg: #3f5f61;
    --tab-icon: #ffffff;
    --alert: #e8452f;
  }
  * { box-sizing: border-box; margin: 0; padding: 0; }
  html, body { width: 677px; height: 1200px; overflow: hidden; }
  body {
    font-family: "Roboto", "Helvetica Neue", Arial, sans-serif;
    background: var(--screen-bg);
    color: var(--ink);
    position: relative;
  }
  .top-bar {
    position: absolute; left: 0; top: 0; width: 677px; height: 140px;
    background: var(--bar-bg);
    border-bottom: 2px solid var(--divider);
  }
  .status-bar {
    position: absolute; left: 0; top: 0; width: 100%; height: 45px;
    font-size: 26px; font-weight: 400;
  }
  .status-bar .carrier { position: absolute; left: 10px; top: 8px; display: flex; align-items: center; gap: 8px; }
  .status-bar .time { position: absolute; left: 0; right: 0; top: 8px; text-align: center; font-weight: 500; }
  .status-bar .power { position: absolute; right: 12px; top: 8px; display: flex; align-items: center; gap: 10px; }
  .screen-title {
    position: absolute; left: 0; right: 0; top: 74px;
    text-align: center; font-size: 38px; font-weight: 500;
  }
  .progress-ring { position: absolute; left: 0; top: 140px; }
  .progress-label {
    position: absolute; left: 153px; top: 432px; width: 370px;
    text-align: center; color: var(--core-text);
    font-size: 40px; font-weight: 300; line-height: 50px;
  }
  .objective-count {
    position: absolute; left: 0; width: 677px; top: 798px;
    text-align: center; font-size: 37px; font-weight: 400;
    padding-left: 30px;
  }
  .tab-bar {
    position: absolute; left: 0; bottom: 0; width: 677px; height: 105px;
    background: var(--tab-bg);
  }
  .tab-bar svg { position: absolute; top: 0; left: 0; }
</style>
</head>
<body>
  <header class="top-bar">
    <div class="status-bar">
      <div class="carrier">
        <svg width="62" height="14" viewBox="0 0 62 14">
          <g fill="#111"><circle cx="6" cy="7" r="5.5"/><circle cx="19" cy="7" r="5.5"/><circle cx="32" cy="7" r="5.5"/></g>
          <g fill="none" stroke="#111" stroke-width="1.5"><circle cx="45" cy="7" r="5"/><circle cx="57" cy="7" r="4.3"/></g>
        </svg>
        <span>NORTH</span>
        <svg width="28" height="22" viewBox="0 0 28 22">
          <path d="M14 20 L9 14 A7 7 0 0 1 19 14 Z" fill="#111"/>
          <path d="M5 10 A13 13 0 0 1 23 10" fill="none" stroke="#111" stroke-width="3"/>
          <path d="M1 5.5 A19 19 0 0 1 27 5.5" fill="none" stroke="#111" stroke-width="3"/>
        </svg>
      </div>
      <div class="time">4:21 PM</div>
      <div class="power">
        <svg width="14" height="26" viewBox="0 0 14 26">
          <path d="M2 7 L12 18 L7 23 L7 3 L12 8 L2 19" fill="none" stroke="#111" stroke-width="2"/>
        </svg>
        <span>22%</span>
        <svg width="52" height="22" viewBox="0 0 52 22">
          <rect x="1" y="1" width="45" height="20" rx="3" fill="none" stroke="#111" stroke-width="2"/>
          <rect x="4" y="4" width="9" height="14" fill="#111"/>
          <rect x="47.5" y="7" width="3.5" height="8" fill="#111"/>
        </svg>
      </div>
    </div>
    <h1 class="screen-title">Home</h1>
  </header>

  <svg class="progress-ring" width="677" height="600" viewBox="0 140 677 600" role="img" aria-label="Objectives progress: 75 percent">
    <path d="M338 287 A210 210 0 1 0 548 497" fill="none" stroke="var(--ring-track)" stroke-width="45" stroke-linecap="round"/>
    <circle cx="338" cy="497" r="185" fill="var(--core)"/>
  </svg>
  <div class="progress-label">75%<br>complete</div>

  <p class="objective-count">9/12 Objectives Complete</p>

  <nav class="tab-bar" aria-label="Main navigation">
    <svg width="677" height="105" viewBox="0 0 677 105">
      <!-- home -->
      <path d="M84 31 L63 51 L68 51 L68 70 L79 70 L79 58 L89 58 L89 70 L100 70 L100 51 L105 51 Z" fill="var(--tab-icon)"/>
      <!-- reports -->
      <g fill="var(--tab-icon)">
        <path d="M252 33 A20 20 0 1 0 274 55 L252 55 Z"/>
        <path d="M257 29 L257 50 L278 50 A21 21 0 0 0 257 29 Z" opacity="0.75"/>
      </g>
      <!-- messages -->
      <g fill="var(--tab-icon)">
        <path d="M406 38 h30 v20 h-18 l-8 7 v-7 h-4 z"/>
        <path d="M424 48 h20 v20 h-3 v6 l-7 -6 h-10 z" opacity="0.85"/>
      </g>
      <g stroke="var(--tab-bg)" stroke-width="2.5">
        <line x1="411" y1="45" x2="431" y2="45"/><line x1="411" y1="51" x2="431" y2="51"/>
      </g>
      <circle cx="442" cy="31" r="6" fill="var(--alert)"/>
      <!-- sign out -->
      <g fill="none" stroke="var(--tab-icon)" stroke-width="3.5">
        <path d="M600 37 L582 37 L582 72 L600 72"/>
        <path d="M590 54 L612 54"/>
      </g>
      <path d="M606 45 L616 54 L606 63 Z" fill="var(--tab-icon)"/>
    </svg>
  </nav>
</body>
</html>
```